Oil and Gas Exploration and Production company needs a business card design

We need a business card design using our logo and colors in the logo. We want a mainstream design.

```html
<!DOCTYPE html>
<html lang="en">
<head>
<meta charset="utf-8">
<title>Corvan Oil &amp; Gas – Business Card</title>
<link href="https://fonts.googleapis.com/css2?family=Lato:wght@400;700&display=swap" rel="stylesheet">
<style>
  :root {
    --backdrop: #cdd2d2;
    --card-dark: #232221;
    --card-light: #f6f6f4;
    --gold: #d49a1c;
    --ink-light: #f2f2f2;
    --ink-dark: #232221;
  }
  * { box-sizing: border-box; margin: 0; padding: 0; }
  html, body {
    width: 1200px; height: 900px; overflow: hidden;
    background: var(--backdrop);
    font-family: "Lato", Arial, sans-serif;
  }
  .stage {
    position: relative; width: 1200px; height: 900px;
    display: flex; align-items: center; justify-content: center; gap: 48px;
  }
  .card {
    position: relative; width: 520px; height: 300px;
    border-radius: 3px; overflow: hidden;
    box-shadow: 0 14px 30px rgba(0,0,0,0.18), 0 2px 4px rgba(0,0,0,0.12);
    border-bottom: 3px solid var(--gold);
  }
  .card-front { display: flex; }
  .front-brand {
    width: 46%; background: var(--card-light);
    display: flex; align-items: center; justify-content: center;
    padding: 0 30px;
  }
  .front-details {
    position: relative; flex: 1; background: var(--card-dark);
    padding: 62px 0 0 44px;
  }
  .front-details::before {
    content: ""; position: absolute; left: 0; top: 80px;
    width: 4px; height: 140px; background: var(--gold);
  }
  .brand {
    display: flex; align-items: center; gap: 12px;
    font-weight: 700; letter-spacing: 0.5px;
  }
  .brand-dot {
    width: 18px; height: 18px; border-radius: 50%; flex: none;
    background: var(--gold);
  }
  .brand-name { line-height: 1.15; }
  .brand-on-light { color: var(--ink-dark); font-size: 28px; }
  .brand-on-light .brand-name { display: block; }
  .brand-on-dark { color: var(--gold); font-size: 30px; white-space: nowrap; }
  .brand-on-dark .brand-dot { width: 20px; height: 20px; }
  .holder-name {
    color: var(--gold); font-size: 24px; font-weight: 400;
    margin-bottom: 22px;
  }
  .contact-list { list-style: none; }
  .contact-list li {
    display: flex; align-items: center; gap: 10px;
    color: var(--ink-light); font-size: 15px; line-height: 26px;
    white-space: nowrap;
  }
  .contact-list svg { width: 13px; height: 13px; flex: none; }
  .card-back {
    background: var(--card-dark);
    display: flex; align-items: center; justify-content: center;
  }
</style>
</head>
<body>
  <main class="stage">
    <section class="card card-front" aria-label="Business card front">
      <div class="front-brand">
        <div class="brand brand-on-light"><span class="brand-dot"></span><span class="brand-name">Corvan<br>Oil &amp; Gas</span></div>
      </div>
      <div class="front-details">
        <h1 class="holder-name">Daniel Reyes</h1>
        <ul class="contact-list">
          <li>
            <svg viewBox="0 0 16 16" aria-hidden="true"><path fill="#d49a1c" d="M3.6 1.2l2.3 2.6-1.3 1.8c.9 2 2.4 3.5 4.5 4.5l1.8-1.3 2.6 2.3-1.1 2.5C7.2 13.4 2.6 8.8 1.2 3.6z"/></svg>
            (555) 310-482-907
          </li>
          <li>
            <svg viewBox="0 0 16 16" aria-hidden="true"><rect x="1.5" y="3.5" width="13" height="9" fill="none" stroke="#d49a1c" stroke-width="1.5"/><path d="M1.5 3.5l6.5 5 6.5-5" fill="none" stroke="#d49a1c" stroke-width="1.5"/></svg>
            info@corvan-oilgas.com
          </li>
          <li>
            <svg viewBox="0 0 16 16" aria-hidden="true"><g fill="none" stroke="#d49a1c" stroke-width="1.3"><circle cx="8" cy="8" r="6.3"/><ellipse cx="8" cy="8" rx="2.8" ry="6.3"/><path d="M1.7 8h12.6M2.8 4.8h10.4M2.8 11.2h10.4"/></g></svg>
            www.corvan-oilgas.com
          </li>
        </ul>
      </div>
    </section>

    <section class="card card-back" aria-label="Business card back">
      <div class="brand brand-on-dark"><span class="brand-dot"></span><span class="brand-name">Corvan Oil &amp; Gas</span></div>
    </section>
  </main>
</body>
</html>
```